Construction business card

I need a new business card, they can connect with my logo, brand.
What we do is residential house , design and build
I like: Navy blue / black
I attached our logo, brand,
and, some idea for business card.

```html
<!DOCTYPE html>
<html lang="en">
<head>
<meta charset="utf-8">
<title>Halvard Building Group – Business Card</title>
<link href="https://fonts.googleapis.com/css2?family=Arimo:wght@400;700&display=swap" rel="stylesheet">
<style>
  :root {
    --page-bg: #3b3b3d;
    --card-bg: #232324;
    --brand-blue: #3a86d0;
    --text-white: #f4f4f4;
    --front-mark: #161617;
  }
  * { box-sizing: border-box; margin: 0; padding: 0; }
  html, body {
    width: 1200px;
    height: 900px;
    overflow: hidden;
    background: var(--page-bg);
    font-family: "Arimo", Arial, sans-serif;
  }
  .canvas {
    position: relative;
    width: 1200px;
    height: 900px;
  }
  .card {
    position: absolute;
    left: 285px;
    width: 630px;
    height: 360px;
    border-radius: 22px;
    background: var(--card-bg);
    box-shadow: 0 10px 30px rgba(0,0,0,.45);
    overflow: hidden;
  }
  .card--front { top: 70px; }
  .card--back  { top: 470px; }

  /* Front: brand name as a tonal spot-gloss mark */
  .front-brand {
    position: absolute;
    inset: 0;
    display: flex;
    flex-direction: column;
    align-items: center;
    justify-content: center;
    gap: 6px;
  }
  .front-brand__name {
    font-weight: 700;
    font-size: 52px;
    letter-spacing: 3px;
    color: var(--front-mark);
    text-transform: uppercase;
    line-height: 1;
  }
  .front-brand__sub {
    font-weight: 700;
    font-size: 24px;
    letter-spacing: 6px;
    color: var(--front-mark);
    text-transform: uppercase;
  }

  /* Back */
  .back-brand {
    position: absolute;
    top: 58px;
    left: 0;
    right: 0;
    display: flex;
    align-items: center;
    justify-content: center;
    gap: 12px;
  }
  .back-brand__square {
    width: 18px;
    height: 18px;
    background: var(--brand-blue);
  }
  .back-brand__name {
    font-weight: 700;
    font-size: 30px;
    letter-spacing: 2px;
    color: var(--text-white);
    text-transform: uppercase;
  }

  .details {
    position: absolute;
    top: 170px;
    left: 0;
    right: 0;
    display: flex;
    justify-content: center;
    align-items: center;
    gap: 22px;
  }
  .person { text-align: right; }
  .person__name {
    font-weight: 700;
    font-size: 27px;
    color: var(--brand-blue);
    text-transform: uppercase;
    letter-spacing: .5px;
  }
  .person__role {
    font-size: 17px;
    color: var(--text-white);
    margin-top: 2px;
  }
  .divider {
    width: 1.5px;
    height: 94px;
    background: var(--brand-blue);
  }
  .contact-list { list-style: none; }
  .contact-list__item {
    display: flex;
    align-items: center;
    gap: 9px;
    font-size: 16px;
    color: var(--text-white);
    line-height: 26px;
  }
  .contact-list__icon { width: 14px; height: 14px; flex: none; }

  .address {
    position: absolute;
    bottom: 52px;
    left: 0;
    right: 0;
    text-align: center;
    font-size: 18px;
    color: var(--text-white);
  }
</style>
</head>
<body>
<main class="canvas">

  <section class="card card--front" aria-label="Card front">
    <div class="front-brand">
      <span class="front-brand__name">Halvard</span>
      <span class="front-brand__sub">Building Group</span>
    </div>
  </section>

  <section class="card card--back" aria-label="Card back">
    <div class="back-brand">
      <span class="back-brand__square"></span>
      <span class="back-brand__name">Halvard Building Group</span>
    </div>

    <div class="details">
      <div class="person">
        <p class="person__name">Daniel Moore</p>
        <p class="person__role">CEO/Founder</p>
      </div>
      <span class="divider"></span>
      <ul class="contact-list">
        <li class="contact-list__item">
          <svg class="contact-list__icon" viewBox="0 0 24 24" aria-hidden="true">
            <path fill="#3a86d0" d="M6.6 10.8a15.1 15.1 0 0 0 6.6 6.6l2.2-2.2c.3-.3.7-.4 1-.2 1.1.4 2.3.6 3.6.6.6 0 1 .4 1 1V20c0 .6-.4 1-1 1A17 17 0 0 1 3 4c0-.6.4-1 1-1h3.5c.6 0 1 .4 1 1 0 1.3.2 2.5.6 3.6.1.3 0 .7-.2 1z"/>
          </svg>
          0400 555 018
        </li>
        <li class="contact-list__item">
          <svg class="contact-list__icon" viewBox="0 0 24 24" aria-hidden="true">
            <rect x="2" y="5" width="20" height="14" rx="2" fill="#3a86d0"/>
            <path d="M3 6l9 7 9-7" fill="none" stroke="#232324" stroke-width="2"/>
          </svg>
          info@halvardbuilding.com.au
        </li>
        <li class="contact-list__item">
          <svg class="contact-list__icon" viewBox="0 0 24 24" aria-hidden="true">
            <circle cx="12" cy="12" r="10" fill="none" stroke="#3a86d0" stroke-width="2.2"/>
            <path d="M2 12h20M12 2c3 3 3 17 0 20M12 2c-3 3-3 17 0 20" fill="none" stroke="#3a86d0" stroke-width="1.8"/>
          </svg>
          halvardbuilding.com.au
        </li>
      </ul>
    </div>

    <p class="address">42 Ferncliff Rd, Oakvale, VIC 3100</p>
  </section>

</main>
</body>
</html>
```